Web Page Design for a Website that Provides Tutoring

I am looking to create an online tutoring website. The website will allow parents or students to contact tutors with a view to instructing them to tutor themselves or their children.

The name of the website is LendYourLessons.

This brief is to create the design for one of the web pages for this web site. I am hoping the same designer will be available to design other pages.

The page I want designed is one of the more complex and I have attached the design as an excel spreadsheet. The web page needs to include all the items on this page but if you want to change the positioning of the items then Im fine with that.

I recently had two logos created for this website. My favourite is the one with a mortar board but im not sure I like the colours. I have attached both of these logos and you can use either of them, change the colours or create something different. I just want a design pleasing to the eye. If the logo is changed I would like that in a seperate file.

So can you please submit designs for this page. I have attached the two logos which you can use, change or if you feel you have a better idea then you can use that.

On the spreadsheet the Send Message, Favourite etc are buttons.

Target Market(s)

People who want to better themselves.
Possible middle class to upper class.

Industry/Entity Type

Tutoring

Number of Pages Required

1 page

Requirements
Must have
• The designs must have alot of the information attached in the spreadsheet.

```html
<!DOCTYPE html>
<html lang="en">
<head>
<meta charset="utf-8">
<title>LendYourLessons – Tutor Profile</title>
<link rel="stylesheet" href="https://fonts.googleapis.com/css2?family=Open+Sans:wght@400;600;700&family=Oswald:wght@500;600&family=Cabin+Sketch:wght@700&family=Playfair+Display:wght@400&display=swap">
<style>
:root{
  --navy:#23233a;
  --footer:#22222c;
  --orange:#f47920;
  --yellow:#f0b400;
  --green:#2fa882;
  --green-dark:#1f7f5e;
  --purple:#545389;
  --purple-dark:#33335e;
  --chalk:#3fb38f;
  --text:#444;
  --muted:#777;
  --line:#dcdcdc;
  --cal-free:#8fd14f;
  --cal-taken:#ff1010;
  --cal-reserved:#f6c192;
  --cal-no:#7030a0;
  --star:#f5b400;
  --red-btn:#e3151a;
}
*{box-sizing:border-box;margin:0;padding:0}
html,body{width:1200px;height:2436px;overflow:hidden}
body{font-family:"Open Sans",Arial,sans-serif;color:var(--text);background:#fff;position:relative}
.abs{position:absolute}
svg.ico{display:inline-block;vertical-align:middle}

/* header */
.site-header{position:absolute;left:0;top:0;width:1200px;height:73px;background:var(--navy)}
.brand{position:absolute;left:73px;top:18px;font-weight:700;font-size:27px;color:var(--orange);letter-spacing:-.3px}
.main-nav{position:absolute;left:404px;top:28px;display:flex;gap:0}
.main-nav a{color:#fff;font-size:13.5px;text-decoration:none;margin-right:38px;position:relative}
.main-nav a.active::after{content:"";position:absolute;left:0;right:0;bottom:-10px;height:2px;background:var(--orange)}
.account{position:absolute;left:993px;top:28px;color:#fff;font-size:13.5px;display:flex;align-items:center;gap:6px}

/* hero */
.hero{position:absolute;left:0;top:73px;width:1200px;height:481px;background:linear-gradient(90deg,#eef1f2 0%,#f7f9f9 60%,#fdfdfd 100%)}
.hero-photo{position:absolute;left:0;top:0;width:700px;height:481px;background:linear-gradient(100deg,#dfe6e8 0%,#eef2f3 40%,#cfd6de 62%,#f2f4f5 100%)}
.hi-bubble{position:absolute;left:598px;top:92px}
.hero-title{position:absolute;left:718px;top:100px;font-family:"Cabin Sketch",cursive;font-size:50px;color:var(--chalk);white-space:nowrap}
.hero-sub{position:absolute;left:720px;top:160px;font-family:"Playfair Display",serif;font-size:36px;color:#555}
.hero-text{position:absolute;left:721px;top:242px;width:410px;font-size:13px;line-height:21px;color:#555}
.hero-actions{position:absolute;left:721px;top:338px;display:flex;gap:11px}
.btn{display:inline-flex;align-items:center;justify-content:center;gap:8px;color:#fff;font-weight:700;font-size:12.5px;text-transform:uppercase;letter-spacing:.3px;border-radius:2px}
.btn-orange{background:var(--orange);width:153px;height:33px}
.btn-green{background:var(--green);width:166px;height:33px}

/* feature panels */
.panel{position:absolute;top:554px;height:310px;width:400px;color:#fff}
.panel-contact{left:0;background:var(--yellow)}
.panel-schedule{left:400px;background:var(--green)}
.panel-reviews{left:800px;background:var(--purple)}
.panel h2{font-family:"Oswald",sans-serif;font-weight:600;font-size:29px;text-transform:uppercase;letter-spacing:-.2px;position:absolute;top:24px}
.panel-contact h2{left:73px}
.panel-reviews h2{left:69px}
.field{position:absolute;left:71px;width:257px;background:#fff;border-radius:2px;color:#555;font-size:12.5px;padding:9px 12px}
.panel-btn{position:absolute;top:239px;height:47px;box-shadow:0 3px 0 rgba(0,0,0,.18);font-size:14px}
.panel-contact .panel-btn{left:71px;width:257px;background:var(--orange)}
.panel-schedule .panel-btn{left:68px;width:255px;background:var(--green-dark)}
.panel-reviews .panel-btn{left:70px;width:257px;background:var(--purple-dark)}
.schedule-intro{position:absolute;left:71px;top:22px;width:250px;font-weight:700;font-size:14.5px;line-height:21px}
.perks{position:absolute;left:71px;top:91px;list-style:none}
.perks li{display:flex;align-items:center;gap:9px;font-size:13px;height:31.5px}
.rating-line{position:absolute;left:69px;top:77px;display:flex;align-items:center;gap:6px;font-size:11.5px}
.bars{position:absolute;left:69px;top:106px;font-size:10.5px}
.bar-row{display:flex;align-items:center;height:15px}
.bar-row span.lbl{width:39px}
.bar-track{width:92px;height:8px;background:#fff}
.bar-fill{height:8px;background:var(--star)}
.bar-row span.pct{margin-left:7px}
.share-line{position:absolute;left:69px;top:206px;font-size:13px}

/* profile stats */
.stats{position:absolute;left:73px;top:918px;width:1053px;height:148px}
.stat-grid{position:absolute;top:0;display:grid;font-size:12.5px;color:#555}
.stat-grid div{height:37px;display:flex;align-items:center;border-bottom:1px solid var(--line)}
.stat-grid div.last{border-bottom:none}
.stats-left{left:0;grid-template-columns:180px 181px 138px;width:499px}
.stats-right{left:554px;grid-template-columns:182px 178px 139px;width:499px}
.stats-divider{position:absolute;left:528px;top:0;width:1px;height:148px;background:var(--line)}
.stats-right .head{font-weight:700;color:#444}
.feedback-btn{background:var(--red-btn);color:#fff;font-weight:700;font-size:12.5px;height:24px;width:138px;border-radius:2px;display:flex;align-items:center;justify-content:center;gap:6px}

/* subject table */
.subjects{position:absolute;left:73px;top:1112px;width:1053px;border-collapse:collapse;font-size:12.5px}
.subjects th{background:#8a8a8a;color:#fff;font-weight:700;text-align:left;height:36px;padding-left:27px}
.subjects td{background:#ececec;height:37px;padding-left:27px;color:#555;border-top:1px solid #f7f7f7}

/* availability */
.section-title{position:absolute;font-weight:700;font-size:18px;color:#333}
.section-title::after{content:"";position:absolute;left:0;bottom:-14px;width:32px;height:3px;background:var(--orange)}
.availability-title{left:73px;top:1278px}
.calendar{position:absolute;left:73px;top:1356px;width:718px;height:414px;border:4px solid #e9e9e9;background:#fff}
.cal-head{position:absolute;left:0;right:0;top:24px;text-align:center;font-weight:600;font-size:17px;color:#333}
.cal-prev{position:absolute;left:78px;top:29px}
.cal-next{position:absolute;right:68px;top:29px}
.cal-grid{position:absolute;left:40px;top:71px;display:grid;grid-template-columns:80px repeat(7,79px);grid-auto-rows:53px;gap:1px;background:#fff;font-size:12px}
.cal-grid div{display:flex;align-items:center;justify-content:center;color:#fff}
.cal-grid .dh{background:#e8e8e8;color:#555;height:52px}
.cal-grid .slot{background:#e8e8e8;color:#555}
.cal-grid .free{background:var(--cal-free)}
.cal-grid .taken{background:var(--cal-taken)}
.cal-grid .reserved{background:var(--cal-reserved)}
.cal-grid .no{background:var(--cal-no)}
.cal-legend{position:absolute;left:794px;top:1356px;width:332px;height:414px;background:var(--navy);padding:40px 46px 0 46px;list-style:none}
.cal-legend li{display:flex;align-items:center;gap:11px;color:#fff;font-size:13px;height:37px;border-bottom:1px solid #34344e}
.cal-legend li:last-child{border-bottom:none}
.swatch{width:13px;height:13px}

/* tutor reviews */
.reviews-title{left:0;width:1200px;text-align:center;top:1822px}
.reviews-title::after{left:584px}
.review{position:absolute;top:1893px;width:340px}
.review h3{font-size:15px;font-weight:700;color:#333}
.review .date{font-size:11px;color:#555;margin-top:6px}
.review p{font-size:12.5px;line-height:20px;color:#555;margin-top:21px}
.review .score{display:flex;align-items:center;gap:2px;font-size:10.5px;color:#555;margin-top:17px}
.review .score span{margin-left:8px}

/* footer */
.site-footer{position:absolute;left:0;top:2092px;width:1200px;height:344px;background:var(--footer);color:#8b8b99;font-size:12.5px}
.site-footer h4{color:#fff;font-size:13.5px;font-weight:700;margin-bottom:14px}
.foot-col{position:absolute;top:36px}
.foot-col p{line-height:21px}
.foot-col ul{list-style:none}
.foot-col li{line-height:26px}
.news-field{width:243px;border-bottom:1px solid #4d4d5a;height:36px;padding-top:16px}
.news-submit{width:243px;height:33px;background:var(--green);color:#fff;font-weight:700;font-size:12.5px;display:flex;align-items:center;justify-content:center;margin-top:17px;text-transform:uppercase}
.social{display:flex;gap:5px;margin-top:22px}
.social span{width:32px;height:32px;border-radius:50%;background:#55556a}
.copyright{position:absolute;left:435px;top:2387px;font-size:12px;color:#6e6e7c}
</style>
</head>
<body>

<svg width="0" height="0" style="position:absolute">
  <defs>
    <symbol id="star" viewBox="0 0 20 20"><polygon points="10,1 12.6,7 19,7.4 14,11.6 15.6,18 10,14.5 4.4,18 6,11.6 1,7.4 7.4,7" fill="#f5b400"/></symbol>
    <symbol id="star-half" viewBox="0 0 20 20"><polygon points="10,1 12.6,7 19,7.4 14,11.6 15.6,18 10,14.5 4.4,18 6,11.6 1,7.4 7.4,7" fill="#ddd"/><polygon points="10,1 10,14.5 4.4,18 6,11.6 1,7.4 7.4,7" fill="#f5b400"/></symbol>
    <symbol id="check" viewBox="0 0 16 16"><circle cx="8" cy="8" r="6.5" fill="none" stroke="#fff" stroke-width="1.5"/><path d="M4.8 8.2l2.2 2.2 4.2-4.4" fill="none" stroke="#fff" stroke-width="1.6"/></symbol>
    <symbol id="pencil" viewBox="0 0 16 16"><path d="M2 14l1-4 8-8 3 3-8 8z" fill="#fff"/></symbol>
  </defs>
</svg>

<header class="site-header">
  <div class="brand">LendYourLessons</div>
  <nav class="main-nav">
    <a class="active">Home</a><a>Search</a><a>Student</a><a>Tutor</a><a>About</a><a>Contact</a>
  </nav>
  <div class="account">
    <svg class="ico" width="14" height="14" viewBox="0 0 14 14"><circle cx="7" cy="4" r="3.2" fill="#f47920"/><path d="M1 14c0-4 2.6-6 6-6s6 2 6 6z" fill="#f47920"/></svg>
    <span>Login&nbsp; or&nbsp; Register</span>
  </div>
</header>

<section class="hero">
  <div class="hero-photo" role="img" aria-label="Photo of a smiling tutor in a business suit writing on a whiteboard in a bright office"></div>
  <svg class="hi-bubble" width="122" height="132" viewBox="0 0 122 132">
    <circle cx="64" cy="60" r="58" fill="#f47920"/>
    <path d="M20 92 L2 130 L46 108 Z" fill="#f47920"/>
    <text x="64" y="76" text-anchor="middle" font-family="Playfair Display, serif" font-size="46" fill="#fff">Hi.</text>
  </svg>
  <div class="hero-title">My name is Selina</div>
  <div class="hero-sub">I am....</div>
  <p class="hero-text">Industry's standard dummy text ever since the 1500s, when an unknown printer took a galley of type and scrambled it to make a type specimen book. It essentially unchanged.</p>
  <div class="hero-actions">
    <span class="btn btn-orange"><svg class="ico" width="13" height="13"><use href="#pencil"/></svg>Register Today</span>
    <span class="btn btn-green"><svg class="ico" width="16" height="11" viewBox="0 0 16 11"><rect x="0" y="1" width="10" height="9" rx="1" fill="#fff"/><path d="M11 5.5l5-4v8z" fill="#fff"/></svg>Watch Our Demo</span>
  </div>
</section>

<section class="panel panel-contact">
  <h2>Contact Tutor</h2>
  <div class="field" style="top:81px;height:36px">Name</div>
  <div class="field" style="top:123px;height:35px">Email</div>
  <div class="field" style="top:164px;height:63px">Message</div>
  <div class="btn panel-btn">
    <svg class="ico" width="22" height="14" viewBox="0 0 22 14"><path d="M0 4h5M2 8h4M0 12h6" stroke="#fff" stroke-width="1.6"/><rect x="8" y="1" width="14" height="12" fill="#fff"/><path d="M8 1l7 6 7-6" fill="none" stroke="#f47920" stroke-width="1.5"/></svg>Send Message
  </div>
</section>

<section class="panel panel-schedule">
  <p class="schedule-intro">She Would like to know your schedule.</p>
  <ul class="perks">
    <li><svg class="ico" width="14" height="14"><use href="#check"/></svg>Offline Lessons</li>
    <li><svg class="ico" width="14" height="14"><use href="#check"/></svg>Affordable Rates</li>
    <li><svg class="ico" width="14" height="14"><use href="#check"/></svg>1-on-1 Tutoring</li>
    <li><svg class="ico" width="14" height="14"><use href="#check"/></svg>Refund Policy</li>
  </ul>
  <div class="btn panel-btn">
    <svg class="ico" width="14" height="15" viewBox="0 0 14 15"><circle cx="7" cy="4" r="3.5" fill="#fff"/><path d="M0 15c0-4 3-6.5 7-6.5s7 2.5 7 6.5z" fill="#fff"/></svg>Contact Favor
  </div>
</section>

<section class="panel panel-reviews">
  <h2>Customer Reviews</h2>
  <div class="rating-line">
    <svg width="84" height="15" viewBox="0 0 84 15"><use href="#star" x="0" width="15" height="15"/><use href="#star" x="17" width="15" height="15"/><use href="#star" x="34" width="15" height="15"/><use href="#star" x="51" width="15" height="15"/><use href="#star" x="68" width="15" height="15"/></svg>
    <span>15 (5.0 out of 5 stars)</span>
  </div>
  <div class="bars">
    <div class="bar-row"><span class="lbl">5 Star</span><div class="bar-track"><div class="bar-fill" style="width:100%"></div></div><span class="pct">100%</span></div>
    <div class="bar-row"><span class="lbl">4 Star</span><div class="bar-track"></div><span class="pct">0%</span></div>
    <div class="bar-row"><span class="lbl">3 Star</span><div class="bar-track"></div><span class="pct">0%</span></div>
    <div class="bar-row"><span class="lbl">2 Star</span><div class="bar-track"></div><span class="pct">0%</span></div>
    <div class="bar-row"><span class="lbl">1 Star</span><div class="bar-track"></div><span class="pct">0%</span></div>
  </div>
  <p class="share-line">Share your thoughts with other customers</p>
  <div class="btn panel-btn"><svg class="ico" width="14" height="14"><use href="#pencil"/></svg>Write a Review</div>
</section>

<section class="stats">
  <div class="stat-grid stats-left">
    <div>Review Score</div><div>4.5/5</div><div>Member Since</div>
    <div>Reliability</div><div>4.0/5.0</div><div>Last Logged In</div>
    <div class="last">Punctuality</div><div class="last">4.6/5</div>
    <div class="last"><span class="feedback-btn"><svg class="ico" width="11" height="11" viewBox="0 0 12 12"><path d="M0 6l12-6-3 12-3-4z" fill="#fff"/></svg>Leave Feedback</span></div>
  </div>
  <div class="stats-divider"></div>
  <div class="stat-grid stats-right">
    <div class="head">Tutoring Type</div><div class="head">In Personal Only</div><div class="head">Teacher</div>
    <div>Willing To Travel</div><div>Home Only</div><div>Full Time Tutor</div>
    <div>Age</div><div>20</div><div>Full Time Student</div>
    <div class="last">DBS (CRB)</div><div class="last"></div><div class="last"></div>
  </div>
</section>

<table class="subjects">
  <colgroup><col style="width:181px"><col style="width:139px"><col style="width:155px"><col style="width:123px"><col style="width:142px"><col style="width:151px"><col></colgroup>
  <thead><tr><th>Subject Taught</th><th>Primary</th><th>Secondary</th><th>GCSE</th><th>A-LEVEL</th><th>University</th><th>Adult Learner</th></tr></thead>
  <tbody>
    <tr><td>Biology</td><td>£20</td><td></td><td>£25</td><td>£30</td><td></td><td></td></tr>
    <tr><td>Chemistry</td><td>£20</td><td></td><td>£25</td><td>£30</td><td></td><td></td></tr>
  </tbody>
</table>

<h2 class="section-title availability-title">Availability</h2>

<div class="calendar">
  <svg class="cal-prev" width="10" height="14" viewBox="0 0 10 14"><path d="M8 1L2 7l6 6" fill="none" stroke="#555" stroke-width="1.6"/></svg>
  <div class="cal-head">November 2016</div>
  <svg class="cal-next" width="10" height="14" viewBox="0 0 10 14"><path d="M2 1l6 6-6 6" fill="none" stroke="#555" stroke-width="1.6"/></svg>
  <div class="cal-grid">
    <div class="dh"></div><div class="dh">S</div><div class="dh">M</div><div class="dh">T</div><div class="dh">W</div><div class="dh">T</div><div class="dh">F</div><div class="dh">S</div>
    <div class="slot">7-8</div><div class="free">30</div><div class="free">31</div><div class="free">1</div><div class="free">2</div><div class="free">3</div><div class="free">4</div><div class="free">5</div>
    <div class="slot">8-9</div><div class="free">6</div><div class="free">7</div><div class="free">8</div><div class="free">9</div><div class="taken">10</div><div class="free">11</div><div class="taken">12</div>
    <div class="slot">4-5</div><div class="no">13</div><div class="free">14</div><div class="taken">15</div><div class="free">16</div><div class="free">17</div><div class="free">18</div><div class="free">19</div>
    <div class="slot">5-6</div><div class="free">20</div><div class="free">21</div><div class="free">22</div><div class="free">23</div><div class="free">24</div><div class="taken">25</div><div class="reserved">26</div>
    <div class="slot">7-8</div><div class="free">27</div><div class="free">28</div><div class="free">29</div><div class="free">30</div><div class="free">1</div><div class="free">2</div><div class="free">3</div>
  </div>
</div>
<ul class="cal-legend">
  <li><span class="swatch" style="background:var(--cal-free)"></span>Available</li>
  <li><span class="swatch" style="background:var(--cal-taken)"></span>Taken</li>
  <li><span class="swatch" style="background:var(--cal-reserved)"></span>Reserved</li>
  <li><span class="swatch" style="background:var(--cal-no)"></span>No</li>
</ul>

<h2 class="section-title reviews-title">Tutors Reviews</h2>

<article class="review" style="left:75px">
  <h3>John Smith</h3>
  <div class="date">12 Dec 2016 | 12:39pm</div>
  <p>" Reference site about Lorem Ipsum, giving information on its origins, as well as a random Lipsum generator."</p>
  <div class="score"><svg width="82" height="14" viewBox="0 0 82 14"><use href="#star" x="0" width="14" height="14"/><use href="#star" x="16" width="14" height="14"/><use href="#star" x="32" width="14" height="14"/><use href="#star" x="48" width="14" height="14"/><use href="#star-half" x="64" width="14" height="14"/></svg><span>(Star Rateing 4.5)</span></div>
</article>
<article class="review" style="left:435px">
  <h3>John Smith</h3>
  <div class="date">12 Dec 2016 | 12:39pm</div>
  <p>" Reference site about Lorem Ipsum, giving information on its origins, as well as a random Lipsum generator."</p>
  <div class="score"><svg width="82" height="14" viewBox="0 0 82 14"><use href="#star" x="0" width="14" height="14"/><use href="#star" x="16" width="14" height="14"/><use href="#star" x="32" width="14" height="14"/><use href="#star" x="48" width="14" height="14"/><use href="#star-half" x="64" width="14" height="14"/></svg><span>(Star Rateing 4.5)</span></div>
</article>
<article class="review" style="left:795px">
  <h3>John Smith</h3>
  <div class="date">12 Dec 2016 | 12:39pm</div>
  <p>" Reference site about Lorem Ipsum, giving information on its origins, as well as a random Lipsum generator."</p>
  <div class="score"><svg width="82" height="14" viewBox="0 0 82 14"><use href="#star" x="0" width="14" height="14"/><use href="#star" x="16" width="14" height="14"/><use href="#star" x="32" width="14" height="14"/><use href="#star" x="48" width="14" height="14"/><use href="#star-half" x="64" width="14" height="14"/></svg><span>(Star Rateing 4.5)</span></div>
</article>

<footer class="site-footer">
  <div class="foot-col" style="left:73px">
    <h4>Get Our Newsletter</h4>
    <p style="width:250px">To receive updates about my tutor, Join our newsletter.</p>
    <div class="news-field">Name</div>
    <div class="news-field">Email</div>
    <div class="news-submit">Submit</div>
  </div>
  <div class="foot-col" style="left:435px">
    <h4>Contact Us</h4>
    <p>228 Lorem Ipsum dolor,<br>Dosis amet, -85485</p>
    <p style="margin-top:21px">T: 1800 555 01<br>E: hello@lendyourlessons.example</p>
    <div class="social"><span></span><span></span><span></span></div>
  </div>
  <div class="foot-col" style="left:705px">
    <h4>Quick Links</h4>
    <ul><li>Home</li><li>Search</li><li>Student</li><li>Tutor</li><li>About</li><li>Contact</li></ul>
  </div>
  <div class="foot-col" style="left:885px">
    <h4>Info Links</h4>
    <ul><li>Register as a Student</li><li>Register as a Paretnt</li><li>Register as a Tutor</li></ul>
  </div>
</footer>
<div class="copyright">Copyright 2016 Lend Your Lessons. All Rights Reserved.</div>

</body>
</html>
```